Stationery Design Project

Need stationery designed for our chicken farming business. We grow chickens in barns for meat production. Looking for all stationery items (business cards, letterhead, envelopes, with compliments etc).

Reason: I am going away for 5 days from Friday 30/3/2012. Won't be able to check designs.

Target Market(s)

The stationery will only be used for correspondence with key stakeholders / suppliers. It is not to be used for marketing etc.

Industry/Entity Type

Business

Requirements
Must have
• I have included all the contact details required for each type of stationery.
Nice to have
• Colours to be used white, green, red, yellow and black (see design).
Should not have
• Rounded Corners.
Centralised information (in centre of business cards / letterhead etc).

```html
<!DOCTYPE html>
<html lang="en">
<head>
<meta charset="utf-8">
<title>Brookvale Poultry – Business Cards</title>
<link rel="stylesheet" href="https://fonts.googleapis.com/css2?family=Source+Sans+3:wght@400;600;700&display=swap">
<style>
  :root {
    --page: #ebe6e0;
    --card-white: #ffffff;
    --green: #2a6b4a;
    --green-deep: #246145;
    --green-light: #8cc7a5;
    --red: #9e1c22;
    --gold: #f5ad2f;
    --grey: #5a5a5a;
    --shadow: 0 4px 10px rgba(0,0,0,0.28);
  }
  * { box-sizing: border-box; margin: 0; padding: 0; }
  html, body { width: 1200px; height: 667px; overflow: hidden; }
  body {
    background: var(--page);
    font-family: "Source Sans 3", "Myriad Pro", Arial, sans-serif;
    position: relative;
  }
  .card {
    position: absolute;
    width: 507px;
    height: 289px;
    box-shadow: var(--shadow);
    overflow: hidden;
  }
  .card--front { background: var(--card-white); }
  .card--front.first { left: 114px; top: 16px; }
  .card--front.second { left: 114px; top: 330px; }
  .card--back {
    left: 650px; top: 19px;
    background: radial-gradient(ellipse at 48% 52%, #5fa07c 0%, var(--green) 45%, var(--green-deep) 100%);
  }
  .waves { position: absolute; inset: 0; width: 100%; height: 100%; }

  .brand {
    position: absolute;
    display: flex;
    align-items: center;
    gap: 10px;
    font-weight: 700;
    line-height: 1.05;
  }
  .brand__dot {
    width: 40px; height: 40px;
    border-radius: 50%;
    flex: none;
  }
  .card--front .brand { left: 36px; top: 78px; color: var(--green); }
  .card--front .brand__dot { background: var(--red); }
  .brand__name { font-size: 30px; }
  .brand__sub { display: block; font-size: 30px; }
  .card--front .brand__name { font-size: 27px; }

  .address {
    position: absolute;
    right: 17px; top: 104px;
    text-align: right;
    font-size: 13px;
    line-height: 17px;
    color: var(--grey);
  }
  .person {
    position: absolute;
    left: 96px; top: 190px;
    display: flex; align-items: center;
    font-size: 13px;
    color: var(--grey);
  }
  .person__name {
    font-size: 17px; font-weight: 700; color: var(--green);
    padding-right: 5px; margin-right: 5px;
    border-right: 1px solid #9a9a9a;
    line-height: 18px;
  }
  .contacts {
    position: absolute;
    right: 12px; top: 222px;
    list-style: none;
    font-size: 13px;
    line-height: 17.5px;
    color: var(--gold);
    text-align: right;
  }
  .contacts li { display: flex; justify-content: flex-end; align-items: center; gap: 9px; }
  .contacts .icon { width: 12px; height: 12px; color: #fff; fill: #fff; font-size: 13px; line-height: 12px; text-align: center; }

  .back-art {
    position: absolute;
    left: 130px; top: 8px;
    width: 300px; height: 220px;
    border-radius: 50%;
    background: radial-gradient(ellipse at center, rgba(120,160,110,0.45) 0%, rgba(40,100,70,0.25) 55%, rgba(40,100,70,0) 75%);
  }
  .card--back .brand {
    left: 132px; top: 145px;
    color: #ffffff;
  }
  .card--back .brand__dot { background: #ffffff; width: 38px; height: 38px; }
  .card--back .brand__name { font-size: 26px; }
</style>
</head>
<body>

  <section class="card card--front first">
    <svg class="waves" viewBox="0 0 525 299" preserveAspectRatio="none" aria-hidden="true">
      <defs>
        <linearGradient id="greenFade1" x1="0" y1="0" x2="1" y2="0">
          <stop offset="0" stop-color="#2a6b4a"/>
          <stop offset="0.6" stop-color="#7dbb97"/>
          <stop offset="1" stop-color="#2a6b4a"/>
        </linearGradient>
      </defs>
      <path d="M0,278 C140,300 320,220 525,165 L525,299 L0,299 Z" fill="url(#greenFade1)"/>
      <path d="M0,245 C70,262 150,285 300,258 C190,295 80,300 0,288 Z" fill="#9e1c22"/>
      <path d="M45,258 C190,300 370,235 525,160 L525,168 C370,245 190,305 45,262 Z" fill="#f5ad2f"/>
    </svg>
    <div class="brand">
      <span class="brand__dot"></span>
      <span class="brand__name">Brookvale<span class="brand__sub">Poultry Pty Ltd</span></span>
    </div>
    <address class="address" style="font-style:normal">Millers Gully Road<br>KENLOW SA 5261</address>
    <div class="person"><span class="person__name">Neil Porter</span>Director</div>
    <ul class="contacts">
      <li>041 200 7314 <svg class="icon" viewBox="0 0 12 12"><path d="M2.5 1 L4.5 1 L5 3.5 L3.8 4.5 C4.5 6 6 7.5 7.5 8.2 L8.5 7 L11 7.5 L11 9.5 C11 10.3 10.3 11 9.5 11 C5 11 1 7 1 2.5 C1 1.7 1.7 1 2.5 1 Z"/></svg></li>
      <li>088 200 4419 <svg class="icon" viewBox="0 0 12 12"><rect x="1" y="4" width="10" height="6" rx="1"/><rect x="3" y="1" width="6" height="3"/></svg></li>
      <li>neilporter@example.com <span class="icon">@</span></li>
    </ul>
  </section>

  <section class="card card--front second">
    <svg class="waves" viewBox="0 0 525 299" preserveAspectRatio="none" aria-hidden="true">
      <defs>
        <linearGradient id="greenFade2" x1="0" y1="0" x2="1" y2="0">
          <stop offset="0" stop-color="#2a6b4a"/>
          <stop offset="0.6" stop-color="#7dbb97"/>
          <stop offset="1" stop-color="#2a6b4a"/>
        </linearGradient>
      </defs>
      <path d="M0,278 C140,300 320,220 525,165 L525,299 L0,299 Z" fill="url(#greenFade2)"/>
      <path d="M0,245 C70,262 150,285 300,258 C190,295 80,300 0,288 Z" fill="#9e1c22"/>
      <path d="M45,258 C190,300 370,235 525,160 L525,168 C370,245 190,305 45,262 Z" fill="#f5ad2f"/>
    </svg>
    <div class="brand">
      <span class="brand__dot"></span>
      <span class="brand__name">Brookvale<span class="brand__sub">Poultry Pty Ltd</span></span>
    </div>
    <address class="address" style="font-style:normal">PO Box 327<br>RIVERTON BEND SA 5272</address>
    <div class="person"><span class="person__name">Neil Porter</span>Director</div>
    <ul class="contacts">
      <li>041 200 7314 <svg class="icon" viewBox="0 0 12 12"><path d="M2.5 1 L4.5 1 L5 3.5 L3.8 4.5 C4.5 6 6 7.5 7.5 8.2 L8.5 7 L11 7.5 L11 9.5 C11 10.3 10.3 11 9.5 11 C5 11 1 7 1 2.5 C1 1.7 1.7 1 2.5 1 Z"/></svg></li>
      <li>088 200 4419 <svg class="icon" viewBox="0 0 12 12"><rect x="1" y="4" width="10" height="6" rx="1"/><rect x="3" y="1" width="6" height="3"/></svg></li>
      <li>neilporter@example.com <span class="icon">@</span></li>
    </ul>
  </section>

  <section class="card card--back">
    <div class="back-art" role="img" aria-label="Large faint emblem artwork behind the company name"></div>
    <div class="brand">
      <span class="brand__dot"></span>
      <span class="brand__name">Brookvale<span class="brand__sub">Poultry Pty Ltd</span></span>
    </div>
  </section>

</body>
</html>
```